Federal IT Consulting Company - Brisolux Consulting Group

We're seeking a skilled web designer to create a modern, bold, and engaging WordPress website for Brisolux Consulting Group, LLC. Our company specializes in federal IT consulting, and our name is a play on "Brightening Solutions." The website should reflect our expertise in the federal technology marketplace and position us as a trusted partner for clients navigating their IT journey.

contact: info@brisoluxgrp-example.com

Current Status

WordPress is already installed on our hosting account
We have an existing logo (may need modernization)

Design Requirements

Style:

Modern and visually striking design
Bold elements to convey confidence and expertise
Incorporate the concept of "brightening solutions" into the design

Features:

Modern UX sliders for dynamic content presentation
Eye-catching, high-quality images (stock photos to be sourced by the designer)
Responsive design for all devices

Color Scheme:

To be proposed by the designer, should align with our brand and convey trust and technological expertise

Logo:

Evaluate our current logo
Create a transparent background version if needed
Propose modernization if deemed necessary

Accessibility:

Ensure design elements are accessible to users with disabilities
Use high contrast ratios for text and background colors
Provide text alternatives for non-text content

Website Structure
Create the following pages, with the possibility of subpages:

Home
Services
About
Contact

Specific Page Requirements
Home Page

Striking hero section with a clear value proposition
Overview of our services
Client testimonials or trust indicators

Services Page

Detailed list of our IT consulting services
Clear explanation of how we help navigate the federal IT landscape

About Page

Company history and mission
Team highlights (if applicable)
Our approach to federal IT consulting

Contact Page

Contact form
Other contact methods (phone, email)

Technical Requirements

Fully responsive design
SEO best practices implemented
Fast loading times
Integration with necessary plugins (to be discussed)
Training on how to update and maintain the site
Full compliance with Web Content Accessibility Guidelines (WCAG) 2.1 Level AA
Adherence to Section 508 standards for federal website accessibility
Implementation of necessary features for ADA compliance
Updates

Designs look the same

Target Market(s)

US Federal Govt customers looking for IT support.

Industry/Entity Type

IT Consulting

Coding

Coded - Design and coding required

Colors
0054AA
0677BA
7BADD7
CADEEF
E8F1F8
0094D4
00A9DD
6FCCEA
C7EBF8
E9F6FB
00AB8E
00BBA5
67D7C9
C6EFE9
E9F9F6

```html
<!DOCTYPE html>
<html lang="en">
<head>
<meta charset="utf-8">
<title>Brisolux Consulting Group — Home</title>
<link rel="stylesheet" href="https://fonts.googleapis.com/css2?family=Audiowide&family=Poppins:wght@400;500;600&display=swap">
<style>
  :root{
    --black:#000000;
    --ink:#ffffff;
    --blue:#0094D4;
    --blue-bright:#00A9DD;
    --blue-light:#7BADD7;
    --sky:#6FCCEA;
    --navy:#0054AA;
    --teal:#00AB8E;
    --teal-bright:#00BBA5;
    --deep-teal:#0b3338;
    --deep-navy:#0a1d33;
    --footer-bar:#222222;
    --display:'Audiowide', sans-serif;
    --body:'Poppins', sans-serif;
  }
  html,body{margin:0;padding:0;background:var(--black);}
  body{width:1200px;height:3918px;overflow:hidden;}
  .page{position:relative;width:1200px;height:3918px;overflow:hidden;background:var(--black);color:var(--ink);font-family:var(--body);}
  .abs{position:absolute;}
  .photo{position:absolute;border-radius:50%;}
  .dot{position:absolute;border-radius:50%;}
  .display{font-family:var(--display);font-weight:400;margin:0;letter-spacing:.5px;}
  .copy{font-size:16px;line-height:38px;margin:0;}
  .btn{position:absolute;display:flex;align-items:center;justify-content:center;border-radius:32px;font-family:var(--display);font-size:18px;letter-spacing:.5px;text-decoration:none;}
  .btn--blue{background:var(--blue);color:var(--ink);}
  .btn--white{background:var(--ink);color:var(--blue);}

  /* header */
  .brand{position:absolute;left:114px;top:72px;display:flex;align-items:center;gap:12px;}
  .brand__mark{width:48px;height:48px;border-radius:50%;background:var(--blue);}
  .brand__name{font-family:var(--display);font-size:38px;color:var(--ink);letter-spacing:1px;white-space:nowrap;}
  .nav{position:absolute;top:86px;left:0;font-size:16px;font-weight:500;}
  .nav a{position:absolute;white-space:nowrap;color:var(--ink);text-decoration:none;}
  .nav a.is-active{color:var(--blue);}
  .search{position:absolute;left:1057px;top:80px;width:34px;height:34px;border-radius:50%;background:var(--ink);display:flex;align-items:center;justify-content:center;}

  /* hero */
  .hero__eyebrow{position:absolute;left:111px;top:231px;font-size:18px;}
  .hero__title{position:absolute;left:111px;top:283px;font-size:22px;color:var(--blue);white-space:nowrap;}
  .hero__copy{position:absolute;left:111px;top:332px;width:430px;}

  /* services */
  .section-title{position:absolute;left:0;width:1200px;text-align:center;font-size:33px;}
  .section-title span{color:var(--blue);}
  .step{position:absolute;width:46px;height:46px;border-radius:50%;border:2px solid var(--blue);box-sizing:border-box;display:flex;align-items:center;justify-content:center;font-family:var(--display);font-size:24px;color:var(--blue);}
  .step--teal{border-color:var(--teal-bright);color:var(--teal-bright);}
  .service__title{position:absolute;font-size:25px;color:var(--blue);white-space:nowrap;}
  .service__title--teal{color:var(--teal-bright);}
  .service__copy{position:absolute;width:430px;}

  /* testimonials */
  .testimonial{position:absolute;left:0;top:2042px;width:1200px;height:427px;}
  .testimonial__panel{position:absolute;left:604px;top:0;width:596px;height:427px;background:var(--blue);}
  .testimonial__title{position:absolute;left:53px;top:128px;font-size:33px;color:var(--ink);white-space:nowrap;}
  .testimonial__copy{position:absolute;left:55px;top:190px;width:430px;}
  .testimonial__name{position:absolute;left:55px;top:320px;font-size:22px;}

  /* about */
  .about__title{position:absolute;left:116px;top:2580px;font-size:32px;}
  .about__title span{color:var(--blue);}
  .about__copy{position:absolute;left:116px;top:2647px;width:430px;}

  /* contact */
  .contact{position:absolute;left:0;top:3062px;width:1200px;height:451px;background:var(--blue);}
  .contact__title{position:absolute;left:0;top:55px;width:1200px;text-align:center;font-size:32px;color:var(--ink);}
  .contact__title span{color:var(--deep-navy);}
  .field{position:absolute;height:56px;border-radius:28px;background:var(--ink);color:#111;display:flex;align-items:center;justify-content:space-between;padding:0 24px;box-sizing:border-box;font-size:15px;font-weight:500;}

  /* footer */
  .footer__col{position:absolute;top:3588px;font-size:13px;}
  .footer__col h4{margin:0 0 24px;font-weight:500;font-size:14px;color:var(--blue);}
  .footer__col a{display:block;color:var(--ink);text-decoration:none;line-height:38px;}
  .footer__bar{position:absolute;left:0;top:3845px;width:1200px;height:73px;background:var(--footer-bar);display:flex;align-items:center;justify-content:center;font-size:17px;}
</style>
</head>
<body>
<div class="page">

  <!-- header -->
  <div class="brand" aria-label="Brisolux Consulting Group">
    <span class="brand__mark"></span>
    <span class="brand__name">BRISOLUX</span>
  </div>
  <nav class="nav">
    <a class="is-active" href="#" style="left:540px;">HOME</a>
    <a href="#" style="left:656px;">SERVICES</a>
    <a href="#" style="left:805px;">ABOUT</a>
    <a href="#" style="left:932px;">CONTACT</a>
  </nav>
  <div class="search" aria-label="Search">
    <svg width="16" height="16" viewBox="0 0 16 16"><circle cx="6.5" cy="6.5" r="4.8" fill="none" stroke="#000" stroke-width="2"/><line x1="10" y1="10" x2="14.5" y2="14.5" stroke="#000" stroke-width="2.2" stroke-linecap="round"/></svg>
  </div>

  <!-- hero -->
  <div class="hero__eyebrow display">WELCOME TO</div>
  <h1 class="hero__title display">BRISOLUX FEDERAL SERVICES</h1>
  <p class="hero__copy copy">Lorem ipsum dolor sit amet, consectetur adipiscing elit, sed do eiusmod tempor incididunt ut labore et dolore magna aliqua.</p>
  <a class="btn btn--blue" href="#" style="left:112px;top:487px;width:203px;height:62px;">GET STARTED</a>

  <div class="abs" role="img" aria-label="Glowing data stream of light particles" style="left:900px;top:0;width:300px;height:260px;background:radial-gradient(ellipse at 80% 20%,rgba(0,169,221,.35),rgba(0,0,0,0) 65%);"></div>
  <div class="dot" style="left:650px;top:220px;width:330px;height:330px;background:var(--deep-navy);"></div>
  <div class="photo" role="img" aria-label="Two colleagues reviewing a tablet in an office" style="left:644px;top:165px;width:162px;height:162px;background:linear-gradient(135deg,#c9cfd6,#5d6670);"></div>
  <div class="photo" role="img" aria-label="Support team members wearing headsets" style="left:824px;top:170px;width:232px;height:232px;background:linear-gradient(135deg,#dfe4ea,#6e7a86);"></div>
  <div class="dot" style="left:551px;top:361px;width:276px;height:276px;background:var(--blue-bright);"></div>
  <div class="photo" role="img" aria-label="Consultant presenting at a laptop" style="left:575px;top:385px;width:228px;height:228px;background:linear-gradient(135deg,#e6e2dc,#7b756d);"></div>
  <div class="photo" role="img" aria-label="Colleagues talking in a bright open office" style="left:854px;top:452px;width:136px;height:136px;background:linear-gradient(135deg,#f0eeea,#a39a8d);"></div>
  <div class="dot" style="left:556px;top:257px;width:72px;height:72px;background:var(--blue);"></div>
  <div class="dot" style="left:817px;top:591px;width:46px;height:46px;background:var(--blue);"></div>
  <div class="dot" style="left:1011px;top:431px;width:80px;height:80px;background:var(--teal-bright);"></div>
  <div class="dot" style="left:814px;top:383px;width:10px;height:10px;background:var(--teal);"></div>

  <!-- services -->
  <h2 class="section-title display" style="top:733px;">OUR <span>SERVICES</span></h2>
  <div class="dot" style="left:1139px;top:742px;width:12px;height:12px;background:var(--blue);"></div>

  <svg class="abs" style="left:0;top:0;" width="1200" height="1700" aria-hidden="true">
    <line x1="707" y1="1103" x2="479" y2="1217" stroke="var(--blue)" stroke-width="2" stroke-dasharray="4 8"/>
    <path d="M502 1564 Q650 1580 806 1600" fill="none" stroke="var(--teal-bright)" stroke-width="2" stroke-dasharray="3 9"/>
  </svg>

  <div class="step" style="left:140px;top:846px;">1</div>
  <h3 class="service__title display" style="left:138px;top:926px;">LOREM IPSUM DOLOR SIT AMET</h3>
  <p class="service__copy copy" style="left:140px;top:985px;">Lorem ipsum dolor sit amet, consectetur adipiscing elit, sed do eiusmod tempor incididunt ut labore et dolore magna aliqua.</p>
  <div class="photo" role="img" aria-label="Engineers working at a computer in a server room" style="left:682px;top:819px;width:364px;height:364px;background:linear-gradient(135deg,#3a6d96,#0e2236);"></div>
  <div class="dot" style="left:669px;top:858px;width:12px;height:12px;background:var(--teal-bright);"></div>

  <div class="photo" role="img" aria-label="Colleagues giving a celebratory high five" style="left:245px;top:1207px;width:364px;height:364px;background:linear-gradient(135deg,#d7dde3,#2c3e57);"></div>
  <div class="step step--teal" style="left:684px;top:1235px;">2</div>
  <h3 class="service__title service__title--teal display" style="left:683px;top:1314px;">LOREM IPSUM DOLOR SIT</h3>
  <p class="service__copy copy" style="left:684px;top:1373px;">Lorem ipsum dolor sit amet, consectetur adipiscing elit, sed do eiusmod tempor incididunt ut labore et dolore magna aliqua.</p>
  <div class="dot" style="left:1078px;top:1238px;width:13px;height:13px;background:var(--blue);"></div>
  <div class="dot" style="left:145px;top:1327px;width:9px;height:9px;background:var(--teal-bright);"></div>

  <div class="step" style="left:140px;top:1638px;">3</div>
  <h3 class="service__title display" style="left:138px;top:1717px;">LOREM IPSUM DOLOR SIT AMET</h3>
  <p class="service__copy copy" style="left:140px;top:1776px;">Lorem ipsum dolor sit amet, consectetur adipiscing elit, sed do eiusmod tempor incididunt ut labore et dolore magna aliqua.</p>
  <div class="photo" role="img" aria-label="Two specialists checking a laptop in a data center" style="left:682px;top:1593px;width:364px;height:364px;background:linear-gradient(135deg,#8fa3b8,#1f3145);"></div>
  <div class="dot" style="left:93px;top:1621px;width:13px;height:13px;background:var(--blue);"></div>
  <div class="dot" style="left:1167px;top:1895px;width:13px;height:13px;background:var(--teal-bright);"></div>

  <!-- testimonials -->
  <section class="testimonial">
    <div class="abs" role="img" aria-label="Smiling client with arms crossed" style="left:0;top:0;width:604px;height:427px;background:linear-gradient(135deg,#b8d9ea,#6fa8cc);"></div>
    <div class="testimonial__panel">
      <svg class="abs" style="left:56px;top:68px;" width="34" height="26" viewBox="0 0 34 26" aria-hidden="true">
        <path d="M2 24 V14 Q2 4 12 2 L13 6 Q7 8 7 13 H13 V24Z M20 24 V14 Q20 4 30 2 L31 6 Q25 8 25 13 H31 V24Z" fill="var(--ink)"/>
      </svg>
      <h2 class="testimonial__title display">CLIENT <span style="color:var(--deep-navy);">TESTIMONIALS</span></h2>
      <p class="testimonial__copy copy">Lorem ipsum dolor sit amet, consectetur adipiscing elit, sed do eiusmod tempor incididunt ut labore et dolore magna aliqua.</p>
      <div class="testimonial__name display">LOREM LIPSUM</div>
      <svg class="abs" style="left:448px;top:350px;" width="130" height="20" viewBox="0 0 130 20" aria-label="Previous and next testimonial">
        <path d="M26 10 H2 M9 3 L2 10 L9 17" fill="none" stroke="var(--ink)" stroke-width="2"/>
        <path d="M90 10 H114 M107 3 L114 10 L107 17" fill="none" stroke="var(--ink)" stroke-width="2"/>
      </svg>
    </div>
  </section>

  <!-- about -->
  <div class="dot" style="left:20px;top:2567px;width:12px;height:12px;background:var(--teal-bright);"></div>
  <h2 class="about__title display">ABOUT <span>US</span></h2>
  <p class="about__copy copy">Lorem ipsum dolor sit amet, consectetur adipiscing elit, sed do eiusmod tempor incididunt ut labore et dolore magna aliqua. Ut enim ad minim veniam, quis nostrud exercitation ullamco laboris nisi ut aliquip ex ea commodo consequat.</p>
  <a class="btn btn--blue" href="#" style="left:112px;top:2875px;width:203px;height:62px;">LEARN MORE</a>
  <div class="dot" style="left:527px;top:2594px;width:6px;height:6px;background:var(--teal-bright);"></div>
  <div class="dot" style="left:406px;top:2883px;width:5px;height:5px;background:var(--teal-bright);"></div>
  <div class="dot" style="left:552px;top:2942px;width:10px;height:10px;background:var(--blue);"></div>
  <div class="dot" style="left:1078px;top:2745px;width:6px;height:6px;background:var(--blue);"></div>
  <div class="dot" style="left:639px;top:2556px;width:136px;height:136px;background:var(--deep-teal);"></div>
  <div class="dot" style="left:895px;top:2785px;width:188px;height:188px;background:var(--deep-teal);"></div>
  <div class="photo" role="img" aria-label="Two colleagues smiling while reviewing documents at a desk" style="left:635px;top:2560px;width:410px;height:410px;background:linear-gradient(135deg,#f1ede8,#9a8a7a);"></div>

  <!-- contact -->
  <section class="contact">
    <h2 class="contact__title display">CONTACT <span>US</span></h2>
    <div class="dot" style="left:974px;top:66px;width:10px;height:10px;background:var(--ink);"></div>
    <div class="dot" style="left:232px;top:112px;width:11px;height:11px;background:var(--ink);"></div>
    <div class="dot" style="left:25px;top:339px;width:10px;height:10px;background:var(--ink);"></div>
    <div class="dot" style="left:1141px;top:344px;width:10px;height:10px;background:var(--ink);"></div>

    <div class="dot" style="left:12px;top:150px;width:50px;height:50px;background:var(--sky);opacity:.6;"></div>
    <div class="dot" style="left:110px;top:230px;width:50px;height:50px;background:var(--sky);opacity:.6;"></div>
    <div class="photo" role="img" aria-label="Two colleagues reviewing paperwork" style="left:16px;top:151px;width:136px;height:136px;background:linear-gradient(135deg,#f0ece6,#8f8374);border:2px solid var(--ink);box-sizing:border-box;"></div>
    <div class="dot" style="left:1040px;top:150px;width:50px;height:50px;background:var(--sky);opacity:.6;"></div>
    <div class="dot" style="left:1136px;top:230px;width:50px;height:50px;background:var(--sky);opacity:.6;"></div>
    <div class="photo" role="img" aria-label="Team meeting around a table in a bright office" style="left:1041px;top:151px;width:136px;height:136px;background:linear-gradient(135deg,#eef2f5,#7f93a6);border:2px solid var(--ink);box-sizing:border-box;"></div>

    <div class="field" style="left:176px;top:143px;width:265px;">NAME
      <svg width="14" height="16" viewBox="0 0 14 16" aria-hidden="true"><circle cx="7" cy="4.5" r="3.8" fill="#111"/><path d="M0 16 Q0 9 7 9 Q14 9 14 16Z" fill="#111"/></svg>
    </div>
    <div class="field" style="left:467px;top:143px;width:265px;">EMAIL ADDRESS
      <svg width="18" height="13" viewBox="0 0 18 13" aria-hidden="true"><rect x="0" y="0" width="18" height="13" rx="1" fill="#111"/><path d="M1 1 L9 7.5 L17 1" fill="none" stroke="#fff" stroke-width="1.4"/></svg>
    </div>
    <div class="field" style="left:756px;top:143px;width:265px;">PHONE NUMBER
      <svg width="16" height="16" viewBox="0 0 16 16" aria-hidden="true"><path d="M3 1 L6 1 L7 5 L5 6.5 Q6.5 9.5 9.5 11 L11 9 L15 10 L15 13 Q15 15 13 15 Q1 14 1 3 Q1 1 3 1Z" fill="#111"/></svg>
    </div>
    <div class="field" style="left:176px;top:222px;width:845px;">MESSAGE
      <svg width="17" height="16" viewBox="0 0 17 16" aria-hidden="true"><path d="M1 1 H16 V11 H6 L2 15 V11 H1Z" fill="#111"/><path d="M4 4.5 H13 M4 7.5 H11" stroke="#fff" stroke-width="1.3"/></svg>
    </div>
    <a class="btn btn--white" href="#" style="left:497px;top:327px;width:204px;height:62px;">SUBMIT NOW</a>
  </section>

  <!-- footer -->
  <div class="brand" aria-label="Brisolux Consulting Group" style="left:134px;top:3650px;">
    <span class="brand__mark"></span>
    <span class="brand__name">BRISOLUX</span>
  </div>
  <div class="footer__col" style="left:560px;">
    <h4>NAVIGATION</h4>
    <a href="#">HOME</a><a href="#">SERVICES</a><a href="#">ABOUT</a><a href="#">CONTACT</a>
  </div>
  <div class="footer__col" style="left:748px;">
    <h4>COMPANY</h4>
    <a href="#">CASE STUDIES</a><a href="#">RESOURCES</a><a href="#">FAQ</a><a href="#">BLOG</a>
  </div>
  <div class="footer__col" style="left:955px;">
    <h4>LINKS</h4>
    <a href="#">PRIVACY POLICY</a><a href="#">TERMS OF USE</a>
  </div>
  <div class="footer__bar">@2024 COPYRIGHTS - ALL RIGHTS RESERVED</div>

</div>
</body>
</html>
```